75%-100% OFF - Insulation Banner Design

Need banners created for an online marketing push for my insulation business Tivoran Energy.

www.tivoranenergy.com

Specifically - I would like the banners to pop utilizing our colors in neon. To see samples of colors we use - visit our asset folder.

https://files.quelmarsh.net/share/7kXpw20LmzQaRt5vYbNe83HsUd4cJf?view=open

I will attach sample files to this project.

The banner must highlight 75%-100% off Insulation and Weatherization. If you can include our current perfect Reviewly somewhere in the advertisement that would be awesome but not a requirement.

The banner must meet Hearthwise logo guidelines. Please see attachment.

Target Market(s)

Home Owners

Industry/Entity Type

Insulation and Construction

Font styles to use
Sans Serif

Colors
59FF00
82FF00
B8FF75
E3FFCB
F4FFEA

Requirements
Must have
• Hearthwise Logo per project description. Must have 75-100% off somewhere that is very clear. And must have our company Tivoran Energy Logo.
Nice to have
• Tivoran Energy Logo

```html
<!DOCTYPE html>
<html lang="en">
<head>
<meta charset="utf-8">
<title>Tivoran Energy — Insulation &amp; Weatherization</title>
<link rel="stylesheet" href="https://fonts.googleapis.com/css2?family=Poppins:wght@400;500;600;700;800&display=swap">
<style>
  :root {
    --neon: #59ff00;
    --lime: #82ff00;
    --mint: #b8ff75;
    --pale: #e3ffcb;
    --white: #ffffff;
    --teal-deep: #1b6a74;
    --teal: #1d8466;
    --green: #27ad33;
    --green-bright: #3fcf1c;
    --divider: rgba(255, 255, 255, 0.55);
  }
  * { margin: 0; padding: 0; box-sizing: border-box; }
  html, body { width: 1200px; height: 629px; overflow: hidden; background: #ffffff; }
  .banner {
    position: relative;
    width: 1200px;
    height: 629px;
    overflow: hidden;
    font-family: "Poppins", sans-serif;
    color: var(--white);
  }
  .banner__photo {
    position: absolute;
    inset: 0;
    background:
      radial-gradient(ellipse 360px 300px at 860px 300px, rgba(120, 230, 150, 0.35) 0%, rgba(120, 230, 150, 0) 100%),
      radial-gradient(ellipse 300px 160px at 760px 560px, rgba(200, 240, 150, 0.25) 0%, rgba(200, 240, 150, 0) 100%),
      linear-gradient(90deg, rgba(10, 50, 40, 0.35) 0%, rgba(10, 50, 40, 0) 55%),
      linear-gradient(180deg, var(--teal-deep) 0%, var(--teal) 40%, var(--green) 75%, var(--green-bright) 100%);
  }
  .brand {
    position: absolute;
    left: 111px;
    top: 62px;
    display: flex;
    align-items: center;
    gap: 14px;
  }
  .brand__mark {
    flex: none;
    width: 38px;
    height: 38px;
    border: 4px solid var(--white);
  }
  .brand__name {
    font-size: 38px;
    font-weight: 600;
    line-height: 1;
    color: var(--white);
  }
  .headline {
    position: absolute;
    left: 108px;
    top: 162px;
    font-size: 54px;
    font-weight: 800;
    line-height: 67px;
    letter-spacing: 0.5px;
    text-transform: uppercase;
  }
  .offer {
    position: absolute;
    right: 60px;
    top: 170px;
    text-align: right;
    text-transform: uppercase;
  }
  .offer__amount {
    display: block;
    font-size: 82px;
    font-weight: 800;
    line-height: 1;
    color: var(--neon);
  }
  .offer__off {
    display: block;
    font-size: 82px;
    font-weight: 800;
    line-height: 1;
    color: var(--white);
  }
  .offer__detail {
    display: block;
    margin-top: 10px;
    font-size: 18px;
    font-weight: 600;
    letter-spacing: 2.4px;
    color: var(--pale);
  }
  .partners {
    position: absolute;
    left: 107px;
    top: 392px;
    height: 106px;
    display: flex;
    align-items: center;
  }
  .partner-program {
    display: flex;
    align-items: center;
    gap: 10px;
    width: 212px;
  }
  .partner-program__mark {
    flex: none;
    width: 24px;
    height: 24px;
    border-radius: 50%;
    background: var(--white);
  }
  .partner-program__name {
    font-size: 28px;
    font-weight: 600;
    line-height: 1;
    white-space: nowrap;
  }
  .partners__divider {
    flex: none;
    width: 1px;
    height: 106px;
    background: var(--divider);
  }
  .review-listing {
    margin-left: 40px;
    font-size: 46px;
    font-weight: 500;
    line-height: 1;
  }
  .contacts {
    position: absolute;
    left: 107px;
    top: 540px;
    display: flex;
    gap: 36px;
  }
  .contact {
    display: flex;
    align-items: center;
    gap: 12px;
  }
  .contact__icon { width: 46px; height: 46px; flex: none; }
  .contact__label {
    display: block;
    font-size: 15px;
    font-weight: 500;
    letter-spacing: 3px;
    text-transform: uppercase;
    line-height: 1;
    margin-bottom: 5px;
  }
  .contact__value {
    display: block;
    font-size: 27px;
    font-weight: 700;
    line-height: 1;
    color: var(--neon);
    text-transform: uppercase;
  }
  .job-code {
    position: absolute;
    left: 1131px;
    top: 572px;
    font-size: 14px;
    font-weight: 600;
  }
</style>
</head>
<body>
  <main class="banner">
    <div class="banner__photo" role="img" aria-label="Insulation installer in goggles and respirator working on his knees in an attic, laying fibreglass batts between rafters, tinted teal to green"></div>

    <div class="brand">
      <span class="brand__mark"></span>
      <span class="brand__name">Tivoran Energy</span>
    </div>

    <h1 class="headline">
      Insulation<br>
      Save Energy<br>
      Weatherization
    </h1>

    <p class="offer">
      <span class="offer__amount">75%–100%</span>
      <span class="offer__off">Off</span>
      <span class="offer__detail">Insulation &amp; Weatherization</span>
    </p>

    <div class="partners">
      <div class="partner-program">
        <span class="partner-program__mark"></span>
        <span class="partner-program__name">Hearthwise</span>
      </div>
      <span class="partners__divider"></span>
      <span class="review-listing">Reviewly</span>
    </div>

    <div class="contacts">
      <div class="contact">
        <svg class="contact__icon" viewBox="0 0 40 40" aria-hidden="true">
          <circle cx="20" cy="20" r="18" fill="none" stroke="#59ff00" stroke-width="2.5"/>
          <path d="M14 12.5c1-.8 2-.7 2.6.3l1.6 2.6c.5.8.3 1.7-.4 2.2l-1.1.8c.9 2 2.6 3.7 4.6 4.6l.8-1.1c.5-.7 1.4-.9 2.2-.4l2.6 1.6c1 .6 1.1 1.6.3 2.6l-1 1.1c-1 1.1-2.7 1.4-4.1.8-4.2-1.8-7.5-5.1-9.3-9.3-.6-1.4-.3-3.1.8-4.1z" fill="#ffffff"/>
        </svg>
        <div>
          <span class="contact__label">Call us any time</span>
          <span class="contact__value">774-555-0186</span>
        </div>
      </div>
      <div class="contact">
        <svg class="contact__icon" viewBox="0 0 40 40" aria-hidden="true">
          <circle cx="20" cy="20" r="18" fill="none" stroke="#59ff00" stroke-width="2.5"/>
          <g fill="none" stroke="#ffffff" stroke-width="1.6">
            <circle cx="20" cy="20" r="9"/>
            <ellipse cx="20" cy="20" rx="4" ry="9"/>
            <line x1="11" y1="20" x2="29" y2="20"/>
            <line x1="12.5" y1="15.5" x2="27.5" y2="15.5"/>
            <line x1="12.5" y1="24.5" x2="27.5" y2="24.5"/>
          </g>
        </svg>
        <div>
          <span class="contact__label">Visit our site</span>
          <span class="contact__value">tivoranenergy.com</span>
        </div>
      </div>
    </div>

    <span class="job-code">C44</span>
  </main>
</body>
</html>
```